Business Card Design

Hello,
I try and keep my business card fresh and current. So about every year i get a new one. This year I'd like something with a white background and black lettering.
Before you start - I do not want my phone number or any other description on the card other than my url and my email.

I'd like a double sided business card with
TomFarrow.com on one side

and

Tom@TomFarrow.com on the other side of the card

Thinking very minimalistic and modern.
I don't have a particular font i mind or how to capitalize my name or website. This card will lead people to my new website that is being designed to showcase my photography and music.

* Initial thought was the front side of the card having a grid-like pattern built out of dashes or periods, with my website sitting within the pattern and on the back side my email on a stark white background. But that might look completely lame - haha.

I'm looking forward to seeing what you come up with.

thank you,
- tom farrow
Updates

Project Deadline Extended
Reason: Want to spend some more time with the designs and add a little $. thanks for all the designs - tom

Project Deadline Extended

Wanted to add a little $ and spend some more time with the designs.

big thanks to all who have submitted work 

- tom

Industry/Entity Type

Business

Contact Information for Business Card

www.tomfarrow.com
tom@tomfarrow.com

Colors
000000
ffffff

Requirements
Must have
• tomfarrow.com
tom@tomfarrow.com
Should not have
• phone number
any description of what i do, photography or music

```html
<!DOCTYPE html>
<html lang="en">
<head>
<meta charset="utf-8">
<title>Tom Farrow – Business Card</title>
<link rel="stylesheet" href="https://fonts.googleapis.com/css2?family=Open+Sans:wght@300;800&display=swap">
<style>
  :root {
    --backdrop: #a4d3cf;
    --card: #ffffff;
    --ink: #000000;
    --ink-soft: #111111;
  }
  html, body {
    margin: 0;
    padding: 0;
    width: 1200px;
    height: 1200px;
    overflow: hidden;
    background: var(--backdrop);
  }
  .canvas {
    position: relative;
    width: 1200px;
    height: 1200px;
  }
  .card {
    position: absolute;
    left: 322px;
    width: 556px;
    height: 346px;
    background: var(--card);
    box-sizing: border-box;
  }
  .card--email { top: 202px; }
  .card--web { top: 672px; }
  .card__frame {
    position: absolute;
    inset: 32px 31px;
    border: 2px dashed var(--ink);
    display: flex;
    align-items: center;
    justify-content: center;
  }
  .card__email {
    margin: 0 0 8px;
    font-family: "Open Sans", sans-serif;
    font-weight: 300;
    font-size: 35px;
    letter-spacing: 0.2px;
    color: var(--ink-soft);
    white-space: nowrap;
  }
  .card__url {
    margin: 4px 0 0;
    font-family: "Open Sans", sans-serif;
    font-weight: 800;
    font-size: 35px;
    letter-spacing: -1.6px;
    color: var(--ink);
    white-space: nowrap;
  }
</style>
</head>
<body>
  <main class="canvas">
    <section class="card card--email">
      <div class="card__frame">
        <p class="card__email">TOM@TOMFARROW.COM</p>
      </div>
    </section>
    <section class="card card--web">
      <div class="card__frame">
        <p class="card__url">WWW.TOMFARROW.COM</p>
      </div>
    </section>
  </main>
</body>
</html>
```